Health Promotion Charity Info-graphic of 2013 Activities

We need an Info-graphic which will be printed on A4 for distribution to our members, government, key stakeholders and grant providers. It will also be uploaded to our website - www.bright-sprouts.com.au

PROJECT BRIEF – Branding as per Bright Sprouts Association
The aim of this infographic is to show the work that Bright Sprouts Association did in 2013. It will be a pictorial annual report. It is to communicate to a wide audience the size and reach of Bright Sprouts Association activities.
We are a health promotion charity that supports schools to deliver healthy food services and our aim is to improve food literacy so kids know what to eat, when.... Our aim is to reduce diet related disease - mainly those relating to overweight and obesity. The infographic should be in keeping with our brand - see www.bright-sprouts.com.au

Using the following information
Our Members
In 2013 we had a total membership of 1,200
Our members are 1,137 Schools
20 Affiliates
24 Individuals
19 Leasees who operate 45 school canteens.
Our school members are
Public Sector Schools 846
Independent Schools 78
Catholic Schools 204
High schools 196
Primary 845
Central schools 30

There are 3082 schools in NSW – so we have 38% as members.

Our services
Supporting Schools
We answered 1078 enquiries through our telephone and email service.
We under took 20 menu assessments
22 school canteens had a business diagnostic
We flew to the regions and attended network meetings and school visits throughout New South Wales: South coast, Central Coast, north coast, illawarra, hunter new England and Dubbo

Publications
We produced the summer and winter editions of Bright Sprouts Tuckshop Corner magazine and
the Annual Bright Sprouts Tuckshop Corner Buyers Guide.

Food Industry
We work with the food industry to change the nutritional value of food
There were 57 food companies that registered 823 food products suitable for school canteens. Of these products, 359 were Green products and 464 amber products.

Community Activities
We worked with Riverbend and Ashgrove councils delivering 8 school holiday cooking classes to 80 children and their parents.

WEBSITE STATS – www.bright-sprouts.com.au
200,381 web visits
157,601 unique visitors
491.495 page views
2.45 pages per visitor

We worked with VOLMO to develop the Crunch Club initiative which resulted in 79,289 phone and tablet Downloads and
10,629 subscribers to the weekly VOLMO email Crunch Club menu and shopping list.

Our funding
Total Income - $1,371,438
Government - $747,870 (54%)
Membership - $83,228 (6%)
Fee for Service – $42,946 (4%)
Other - $497,395(36%)
Total Equity $50,811

0555a3
9bcb3c
0593ce

```html
<!DOCTYPE html>
<html lang="en">
<head>
<meta charset="utf-8">
<title>Bright Sprouts Association – 2013 in Review</title>
<link rel="stylesheet" href="https://fonts.googleapis.com/css2?family=Montserrat:wght@700;800&family=Open+Sans:wght@300;400;600;700&family=Noto+Serif:wght@400;700&display=swap">
<style>
  :root {
    --navy: #0555a3;
    --sky: #0593ce;
    --lime: #9bcb3c;
    --white: #ffffff;
    --rule: #e3e3e3;
  }
  * { margin: 0; padding: 0; box-sizing: border-box; }
  html, body { width: 849px; height: 1200px; overflow: hidden; background: var(--white); }
  .sheet { position: relative; width: 849px; height: 1200px; overflow: hidden; background: var(--white); font-family: 'Open Sans', sans-serif; }
  .abs { position: absolute; }
  .heading { font-family: 'Montserrat', sans-serif; font-weight: 800; text-transform: uppercase; letter-spacing: 0.3px; line-height: 1; }
  .copy { font-weight: 300; font-size: 16px; line-height: 17px; color: var(--white); }
  .copy b { font-weight: 700; }

  .shapes { position: absolute; inset: 0; }

  .title-ribbon-text { left: 46px; top: 62px; color: var(--white); font-size: 33px; }

  .brand { left: 46px; top: 170px; width: 170px; display: flex; flex-direction: column; align-items: center; gap: 10px; }
  .brand-dot { width: 96px; height: 96px; border-radius: 50%; background: var(--lime); }
  .brand-name { font-family: 'Montserrat', sans-serif; font-weight: 700; font-size: 20px; color: var(--sky); }
  .brand-rule { left: 223px; top: 145px; width: 1px; height: 158px; background: var(--rule); }

  .services { left: 537px; top: 36px; width: 290px; }
  .services .heading { color: var(--white); font-size: 25px; }

  .members { left: 46px; top: 326px; width: 380px; color: var(--navy); }
  .members .heading { font-size: 31px; margin-bottom: 4px; }
  .members p { font-family: 'Noto Serif', serif; font-size: 15.5px; line-height: 17.3px; }
  .members p b { font-family: 'Open Sans', sans-serif; font-weight: 700; }
  .members .gap { margin-top: 17px; }

  .publications { left: 484px; top: 301px; width: 340px; }
  .publications .heading, .food .heading { color: var(--white); font-size: 25px; }
  .food { left: 484px; top: 465px; width: 340px; }

  .community { left: 242px; top: 690px; width: 580px; }
  .community .heading { color: var(--white); font-size: 24px; margin-bottom: 8px; }

  .web { left: 450px; top: 847px; width: 380px; color: var(--white); }
  .web .heading { font-size: 24px; }
  .web .url { font-family: 'Noto Serif', serif; font-size: 15px; margin-top: 1px; }
  .stat { position: absolute; display: flex; gap: 8px; align-items: flex-start; }
  .stat svg { flex: none; margin-top: 3px; }
  .stat b { display: block; font-family: 'Montserrat', sans-serif; font-weight: 700; font-size: 16px; line-height: 16px; }
  .stat span { font-family: 'Noto Serif', serif; font-size: 15.5px; line-height: 17px; }

  .crunch { left: 47px; top: 992px; width: 250px; color: var(--white); font-size: 15.5px; line-height: 22.5px; font-weight: 300; }

  .funding-label { left: 334px; top: 1122px; width: 152px; text-align: center; color: var(--white); font-size: 22px; line-height: 28px; }
  .funding-sign { left: 334px; top: 1020px; width: 152px; text-align: center; color: var(--white); font-family: 'Open Sans', sans-serif; font-weight: 300; font-size: 80px; line-height: 1; }
  .funding { left: 560px; top: 1054px; color: var(--white); font-family: 'Noto Serif', serif; font-size: 15.5px; line-height: 20.5px; }
  .funding b { font-family: 'Open Sans', sans-serif; font-weight: 700; }
</style>
</head>
<body>
<div class="sheet">
  <svg class="shapes" width="849" height="1200" viewBox="0 0 849 1200" aria-hidden="true">
    <!-- title ribbon -->
    <path d="M0 37 H378 L396 80 L378 124 H0 Z" fill="var(--navy)"/>
    <path d="M0 45 H372 L386 80 L372 116 H0" fill="none" stroke="var(--white)" stroke-width="1.2" stroke-dasharray="5 4"/>
    <!-- services panel -->
    <path d="M456 0 H849 V250 H458 A210 210 0 0 0 456 0 Z" fill="var(--navy)"/>
    <!-- publications -->
    <rect x="451" y="283" width="398" height="129" fill="var(--sky)"/>
    <!-- food industry -->
    <rect x="451" y="448" width="398" height="182" fill="var(--lime)"/>
    <!-- community -->
    <rect x="0" y="663" width="849" height="134" fill="var(--sky)"/>
    <g fill="none" stroke="var(--white)" stroke-width="5">
      <polyline points="123,764 147,722 178,750 198,691"/>
      <circle cx="123" cy="764" r="10" fill="var(--sky)"/>
      <circle cx="147" cy="722" r="10" fill="var(--sky)"/>
      <circle cx="178" cy="750" r="10" fill="var(--sky)"/>
      <circle cx="198" cy="691" r="10" fill="var(--sky)"/>
    </g>
    <!-- website band -->
    <path d="M380 833 H849 V985 H332 L305 958 V930 Z" fill="var(--lime)"/>
    <circle cx="352" cy="876" r="68" fill="var(--lime)" stroke="var(--white)" stroke-width="5"/>
    <circle cx="352" cy="876" r="55" fill="none" stroke="var(--white)" stroke-width="1.5" stroke-dasharray="3 3"/>
    <g fill="none" stroke="var(--white)" stroke-width="3">
      <circle cx="352" cy="876" r="30"/>
      <ellipse cx="352" cy="876" rx="13" ry="30"/>
      <line x1="322" y1="876" x2="382" y2="876"/>
      <line x1="327" y1="862" x2="377" y2="862"/>
      <line x1="327" y1="890" x2="377" y2="890"/>
      <line x1="352" y1="846" x2="352" y2="906"/>
    </g>
    <!-- big navy circle -->
    <circle cx="55" cy="1070" r="250" fill="var(--navy)"/>
    <g stroke="var(--white)" stroke-linecap="round" fill="none">
      <line x1="60" y1="905" x2="125" y2="960" stroke-width="9"/>
      <circle cx="56" cy="902" r="11" stroke-width="6"/>
      <line x1="118" y1="900" x2="62" y2="958" stroke-width="8"/>
      <line x1="125" y1="893" x2="135" y2="883" stroke-width="6"/>
    </g>
    <!-- funding -->
    <path d="M420 1033 H849 V1200 H420 Z" fill="var(--sky)"/>
    <circle cx="410" cy="1118" r="92" fill="var(--navy)" stroke="var(--white)" stroke-width="6"/>
  </svg>

  <div class="abs heading title-ribbon-text">2013 in Review</div>

  <div class="abs brand">
    <div class="brand-dot"></div>
    <div class="brand-name">Bright Sprouts</div>
  </div>
  <div class="abs brand-rule"></div>

  <section class="abs services">
    <h2 class="heading">Our Services</h2>
    <p class="copy">Supporting Schools<br>We answered <b>1078</b> enquiries through our telephone and email service. We under took <b>20</b> menu assessments <b>22</b> school canteens had a business diagnostic. We flew to the regions and attended network meetings and school visits throughout New South Wales</p>
  </section>

  <section class="abs members">
    <h2 class="heading">Our Members</h2>
    <p>In 2013 we had a total membership of 1,200<br><b>1,137</b> Schools Members<br><b>20</b> Affiliates<br><b>24</b> Individuals<br><b>19</b> Leasees who operate 45 school canteens.</p>
    <p class="gap">Our school members are<br><b>846</b> Public Sector Schools<br><b>78</b> Independent Schools<br><b>204</b> Catholic Schools<br><b>196</b> High schools<br><b>845</b> Primary<br><b>30</b> Central schools</p>
    <p class="gap">There are 3082 schools in NSW –<br>so we have 38% as members.</p>
  </section>

  <section class="abs publications">
    <h2 class="heading">Publications</h2>
    <p class="copy">We produced the summer and winter editions of Bright Sprouts Tuckshop Corner magazine and the Annual Bright Sprouts Tuckshop Corner Buyers Guide.</p>
  </section>

  <section class="abs food">
    <h2 class="heading">Food Industry</h2>
    <p class="copy">We work with the food industry to change the nutritional value of food<br>There were <b>57</b> food companies that registered <b>823</b> food products suitable for school canteens. Of these products, <b>359</b> were Green products and <b>464</b> amber products.</p>
  </section>

  <section class="abs community">
    <h2 class="heading">Community Activities</h2>
    <p class="copy" style="line-height:22px">We worked with Riverbend and Ashgrove councils delivering<br><b>8</b> school holiday cooking classes to <b>80</b> children and their parents.</p>
  </section>

  <section class="abs web">
    <h2 class="heading">Website Stats</h2>
    <div class="url">www.bright-sprouts.com.au</div>
  </section>
  <div class="stat" style="left:450px;top:900px;color:#fff">
    <svg width="24" height="24" viewBox="0 0 24 24"><circle cx="12" cy="12" r="11" fill="#fff"/><circle cx="12" cy="12" r="5" fill="none" stroke="var(--lime)" stroke-width="2"/></svg>
    <div><b>200,381</b><span>web visits</span></div>
  </div>
  <div class="stat" style="left:450px;top:943px;color:#fff">
    <svg width="24" height="24" viewBox="0 0 24 24"><circle cx="12" cy="12" r="11" fill="#fff"/><circle cx="12" cy="9" r="3.5" fill="var(--lime)"/><path d="M6 18 Q12 11 18 18 Z" fill="var(--lime)"/></svg>
    <div><b>157,601</b><span>unique visitors</span></div>
  </div>
  <div class="stat" style="left:614px;top:900px;color:#fff">
    <svg width="28" height="28" viewBox="0 0 28 28"><circle cx="14" cy="14" r="12" fill="none" stroke="#fff" stroke-width="2.5"/><polyline points="8,14 12.5,18.5 20,10" fill="none" stroke="#fff" stroke-width="2.5"/></svg>
    <div><b>491.495</b><span>page views</span></div>
  </div>
  <div class="stat" style="left:614px;top:943px;color:#fff">
    <svg width="28" height="28" viewBox="0 0 28 28"><circle cx="14" cy="14" r="12" fill="none" stroke="#fff" stroke-width="2.5"/><circle cx="12.5" cy="12.5" r="4.5" fill="none" stroke="#fff" stroke-width="2.2"/><line x1="16" y1="16" x2="20" y2="20" stroke="#fff" stroke-width="2.5"/></svg>
    <div><b>2.45</b><span>pages per visitor</span></div>
  </div>

  <p class="abs crunch">We worked with VOLMO to develop the Crunch Club initiative which resulted in <b style="font-weight:700">79,289</b> phone and tablet Downloads and <b style="font-weight:700">10,629</b> subscribers to the weekly VOLMO email Crunch Club menu and shopping list.</p>

  <div class="abs funding-sign">$</div>
  <div class="abs heading funding-label">Our<br>Funding</div>
  <p class="abs funding">
    <b>$1,371,438</b> Total Income<br>
    <b>$747,870 (54%)</b> Government<br>
    <b>$83,228 (6%)</b> Membership<br>
    <b>$42,946 (4%)</b> Fee for Service<br>
    <b>$497,395(36%)</b> Other<br>
    <b>$50,811</b> Total Equity
  </p>
</div>
</body>
</html>
```